Refer a Friend A5 Flyer for Healthcare Staff

We need an A5 flyer that we can hand out to existing and new staff members promoting our Refer a friend Scheme. We need the leaflet to encourage staff to talk to their family and friends about joining our Healthcare Agency, which provides staff to local care related establishments. Using our logo and brand colours blue and green, as per our website, the final design will need to clearly convey the benefits and attractions of referring additional staff to the team. In addition is the promotion of our Chatterbook page, requesting staff to like the page and to like and share various posts.

Target Market(s)

Healthcare and potential Healthcare Staff

Industry/Entity Type

Healthcare

Colors
33b8a4
3277b5

Requirements
Must have
• Company Logo, Brand colours,
• text; "Refer a Friend and receive a £50 Bonus after just 1 completed shift"
• text; "3 easy steps to refer a friend, 1 Fill out your name on the back of your Business Card 2 Hand the card to your friend or any person you wish to refer, 3 ask your friend to present the card to us when they attend their interview"
• text; "Like and share any of our Open Days on Chatterbook for a chance to win a prize, you can find us easily by searching @CarewellStaffingPartners"
• text; "Like our Page to stay up to date with our events and offers"
Nice to have
• care worker / elderly care / support worker pictures
• Content / pics from website www.carewellstaffingpartners.co.uk

```html
<!DOCTYPE html>
<html lang="en">
<head>
<meta charset="utf-8">
<title>Refer a Friend Flyer – Carewell Staffing</title>
<link rel="stylesheet" href="https://fonts.googleapis.com/css2?family=Oswald:wght@400;500;600&family=Roboto+Condensed:wght@300;400&family=Questrial&display=swap">
<style>
  :root {
    --green: #62b19a;
    --blue: #4570b1;
    --ink: #2b2b2b;
    --paper: #f7f7f7;
    --disc: #f1f1f1;
    --frame-grey: #cfcfd1;
    --backdrop: #ecebe8;
    --shadow-grey: #b9b9b9;
  }
  * { box-sizing: border-box; margin: 0; padding: 0; }
  html, body { width: 1182px; height: 1200px; overflow: hidden; }
  body {
    background: var(--backdrop);
    font-family: "Roboto Condensed", "Arial Narrow", sans-serif;
    color: var(--ink);
  }
  .flyer {
    position: absolute;
    left: 188px; top: 20px;
    width: 806px; height: 1160px;
    background: var(--paper);
    display: flex; flex-direction: column;
    overflow: hidden;
  }
  .brand-header {
    height: 106px; flex: none;
    display: flex; align-items: center; justify-content: center; gap: 10px;
    border-bottom: 3px solid var(--blue);
  }
  .brand-dot { width: 22px; height: 22px; border-radius: 50%; background: var(--green); }
  .brand-name {
    font-family: "Questrial", sans-serif;
    font-size: 34px; color: var(--blue); letter-spacing: .5px;
  }
  .hero-photo {
    height: 337px; flex: none;
    background: linear-gradient(100deg, #e8e4da 0%, #cfc1b0 30%, #d9d3cb 50%, #f1f1ef 70%, #e2dccf 100%);
  }
  .offer-band {
    height: 141px; flex: none;
    background: var(--green);
    color: #fff; text-align: center;
    padding-top: 6px;
  }
  .offer-url { font-weight: 300; font-size: 17px; letter-spacing: .3px; }
  .offer-line {
    font-family: "Oswald", sans-serif; font-weight: 400;
    text-transform: uppercase; line-height: 1.1;
  }
  .offer-line--top { font-size: 35px; margin-top: 4px; }
  .offer-line--bottom { font-size: 35px; }
  .offer-amount { font-size: 55px; font-weight: 600; margin-right: 6px; }
  .steps-title {
    height: 50px; flex: none; background: var(--blue);
    color: #fff; text-align: center;
    font-family: "Oswald", sans-serif; font-weight: 400; font-size: 29px; line-height: 50px;
  }
  .steps {
    height: 248px; flex: none;
    display: flex; justify-content: center;
    padding: 8px 30px 0;
  }
  .step { width: 230px; text-align: center; }
  .step svg { display: block; margin: 0 auto; }
  .step-text { font-size: 20px; font-weight: 300; line-height: 1.2; margin: 2px auto 0; width: 210px; }
  .step-divider {
    width: 0; height: 200px; margin: 18px 12px 0;
    border-left: 2px dashed var(--blue);
  }
  .gallery {
    height: 157px; flex: none;
    display: flex; gap: 6px; padding: 0 26px;
  }
  .gallery-photo { flex: 1; border: 6px solid var(--frame-grey); }
  .gallery-photo--park { background: linear-gradient(180deg, #5e7a3a 0%, #8aa650 45%, #d6c640 80%, #6c5ca8 100%); }
  .gallery-photo--path { background: linear-gradient(180deg, #7d9a5e 0%, #a6bd7f 45%, #8fb556 75%, #c7b39b 100%); }
  .social-note {
    height: 64px; flex: none; text-align: center;
    font-size: 20px; font-weight: 300; line-height: 1.35;
    padding-top: 6px;
  }
  .social-handle { color: var(--blue); font-size: 23px; }
  .footer-band {
    flex: 1; background: var(--green); color: #fff;
    text-align: center; font-weight: 300; font-size: 19px;
    display: flex; align-items: center; justify-content: center;
  }
</style>
</head>
<body>
<main class="flyer">
  <header class="brand-header">
    <span class="brand-dot"></span>
    <span class="brand-name">Carewell Staffing</span>
  </header>

  <div class="hero-photo" role="img" aria-label="Photo of a smiling care worker in a white tunic walking arm in arm with an elderly woman"></div>

  <section class="offer-band">
    <p class="offer-url">www.carewellstaffingpartners.co.uk</p>
    <p class="offer-line offer-line--top">Refer a friend and receive a</p>
    <p class="offer-line offer-line--bottom"><span class="offer-amount">£50 Bonus</span>after just 1 completed shift</p>
  </section>

  <h2 class="steps-title">3 easy steps to refer a friend</h2>

  <section class="steps">
    <div class="step">
      <svg width="190" height="150" viewBox="0 0 190 150" aria-hidden="true">
        <defs><clipPath id="ring-clip-1"><circle cx="112" cy="74" r="68"/></clipPath></defs>
        <text x="28" y="130" font-family="Oswald, sans-serif" font-size="128" font-weight="500" fill="var(--paper)" stroke="var(--green)" stroke-width="3">1</text>
        <polygon clip-path="url(#ring-clip-1)" points="76,96 136,42 200,110 150,170 100,150" fill="var(--shadow-grey)" opacity=".65"/>
        <circle cx="106" cy="70" r="42" fill="var(--disc)"/>
        <circle cx="112" cy="74" r="68" fill="none" stroke="var(--green)" stroke-width="3"/>
        <rect x="86" y="57" width="40" height="28" rx="4" fill="none" stroke="var(--green)" stroke-width="2.5"/>
        <line x1="86" y1="65" x2="126" y2="65" stroke="var(--green)" stroke-width="2.5"/>
        <line x1="91" y1="77" x2="107" y2="77" stroke="var(--green)" stroke-width="2.5"/>
        <circle cx="118" cy="77" r="3" fill="none" stroke="var(--green)" stroke-width="2"/>
      </svg>
      <p class="step-text">Fill out your name on the back of your Business Card</p>
    </div>
    <div class="step-divider"></div>
    <div class="step">
      <svg width="190" height="150" viewBox="0 0 190 150" aria-hidden="true">
        <defs><clipPath id="ring-clip-2"><circle cx="112" cy="74" r="68"/></clipPath></defs>
        <text x="20" y="130" font-family="Oswald, sans-serif" font-size="128" font-weight="500" fill="var(--paper)" stroke="var(--blue)" stroke-width="3">2</text>
        <polygon clip-path="url(#ring-clip-2)" points="76,96 136,42 200,110 150,170 100,150" fill="var(--shadow-grey)" opacity=".65"/>
        <circle cx="106" cy="70" r="42" fill="var(--disc)"/>
        <circle cx="112" cy="74" r="68" fill="none" stroke="var(--blue)" stroke-width="3"/>
        <rect x="84" y="52" width="38" height="26" rx="3" fill="none" stroke="var(--green)" stroke-width="2.5"/>
        <line x1="89" y1="70" x2="107" y2="70" stroke="var(--green)" stroke-width="2"/>
        <path d="M112 70 l8 -4 l10 12 v18 h-14 l-8 -12 z" fill="var(--disc)" stroke="var(--green)" stroke-width="2.5" stroke-linejoin="round"/>
      </svg>
      <p class="step-text">Hand the card to your friend or any person you wish to refer</p>
    </div>
    <div class="step-divider"></div>
    <div class="step">
      <svg width="190" height="150" viewBox="0 0 190 150" aria-hidden="true">
        <defs><clipPath id="ring-clip-3"><circle cx="112" cy="74" r="68"/></clipPath></defs>
        <text x="20" y="130" font-family="Oswald, sans-serif" font-size="128" font-weight="500" fill="var(--paper)" stroke="var(--green)" stroke-width="3">3</text>
        <polygon clip-path="url(#ring-clip-3)" points="76,96 136,42 200,110 150,170 100,150" fill="var(--shadow-grey)" opacity=".65"/>
        <circle cx="106" cy="70" r="42" fill="var(--disc)"/>
        <circle cx="112" cy="74" r="68" fill="none" stroke="var(--green)" stroke-width="3"/>
        <circle cx="93" cy="58" r="6" fill="none" stroke="var(--green)" stroke-width="2.5"/>
        <circle cx="119" cy="58" r="6" fill="none" stroke="var(--green)" stroke-width="2.5"/>
        <path d="M83 78 a10 10 0 0 1 20 0" fill="none" stroke="var(--green)" stroke-width="2.5"/>
        <path d="M109 78 a10 10 0 0 1 20 0" fill="none" stroke="var(--green)" stroke-width="2.5"/>
        <line x1="79" y1="80" x2="133" y2="80" stroke="var(--green)" stroke-width="2.5"/>
        <line x1="85" y1="80" x2="85" y2="92" stroke="var(--green)" stroke-width="2.5"/>
        <line x1="127" y1="80" x2="127" y2="92" stroke="var(--green)" stroke-width="2.5"/>
      </svg>
      <p class="step-text">Ask your friend to present the card to us when they attend their interview</p>
    </div>
  </section>

  <section class="gallery">
    <div class="gallery-photo gallery-photo--park" role="img" aria-label="Photo of a carer pushing an elderly man in a wheelchair through a flower garden"></div>
    <div class="gallery-photo gallery-photo--path" role="img" aria-label="Photo of a care worker with an elderly woman in a wheelchair on a park path"></div>
  </section>

  <p class="social-note">Like and share any of our Open Days on Chatterbook for a chance to win a prize,<br>you can find us easily by searching <span class="social-handle">@CarewellStaffingPartners</span></p>

  <footer class="footer-band">Like our Page to stay up to date with our events and offers</footer>
</main>
</body>
</html>
```